Financial Services Consultant needs a business card

We need a business card for a new consulting company based in Melbourne called
"Quelbrook Insights". Tagline is TRACK, REVIEW, RETAIN
We would like to see business card designs that are in line with the minimal style of the website www.quelbrook-insights.example
The font I have used on the website is Proxima Nova and would like the same or similar font used on the business card with a minimal design in line with the website Two sided with "QUELBROOK INSIGHTS" TRACK, REVIEW, RETAIN on one side and name, title and contact details on the otther
Updates

Hi All, thanks for your submissions, much appreciated.

I have recently added some colour to my webiste, it is hex #3a7b74 for those that wish to use it
Thanks

Hi all

thanks very much for your design submissions I am very impressed and they are much appreciated.

Interms of general feedback please find below;

Colour: I am trying to stick to a minimal design and colour scheme for my website which is still under construction, up to 3 colours( www.quelbrook-insights.example) it is currently black and white with a small amount of blue/green but I am open to suggestion/interpretations for a consulting company.

Card: I dont mind if it has rounded edges or straight, I was thinking about using a letterpress card if possible

Detail: the detail on the card will include; Name, Title, Mobile, Personal Email, Business Email,Web,Business Address

Once again thanks for submissions

Industry/Entity Type

Business

```html
<!DOCTYPE html>
<html lang="en">
<head>
<meta charset="utf-8">
<title>Quelbrook Insights — Business Card</title>
<link rel="stylesheet" href="https://fonts.googleapis.com/css2?family=Montserrat:wght@400;500;600;700&display=swap">
<style>
  :root {
    --stage: #e9e7e3;
    --card-light: #ffffff;
    --card-dark: #3b3b3b;
    --ink: #141414;
    --ink-inverse: #ffffff;
    --accent: #5fae9c;
    --shadow: rgba(0, 0, 0, 0.18);
  }
  * { box-sizing: border-box; margin: 0; padding: 0; }
  html, body {
    width: 1200px;
    height: 837px;
    overflow: hidden;
    background: var(--stage);
    font-family: "Montserrat", Arial, sans-serif;
  }
  .canvas {
    position: relative;
    width: 1200px;
    height: 837px;
  }
  .card {
    position: absolute;
    width: 560px;
    height: 320px;
    border-radius: 4px;
    box-shadow: 0 10px 28px var(--shadow);
    overflow: hidden;
  }

  /* Brand side */
  .card--front {
    left: 70px;
    top: 440px;
    background: var(--card-light);
    color: var(--ink);
    display: flex;
    flex-direction: column;
    justify-content: center;
    padding-left: 40px;
  }
  .brand-name {
    font-size: 38px;
    font-weight: 500;
    letter-spacing: 1.5px;
    line-height: 1;
    white-space: nowrap;
  }
  .tagline {
    margin-top: 22px;
    padding-left: 36px;
    font-size: 15px;
    font-weight: 600;
    letter-spacing: 1px;
  }

  /* Contact side */
  .card--back {
    left: 570px;
    top: 80px;
    background: var(--card-dark);
    color: var(--ink-inverse);
  }
  .accent-bar {
    position: absolute;
    width: 20px;
    background: var(--accent);
  }
  .accent-bar--left { left: 0; top: 92px; height: 96px; }
  .accent-bar--right { right: 0; top: 150px; height: 110px; }
  .person {
    position: absolute;
    left: 0; right: 0;
    top: 44px;
    text-align: center;
  }
  .person__name {
    font-size: 30px;
    font-weight: 500;
    letter-spacing: 0.5px;
  }
  .person__title {
    margin-top: 12px;
    font-size: 18px;
    font-weight: 400;
  }
  .contact {
    position: absolute;
    font-size: 14px;
    font-weight: 500;
    line-height: 1.4;
    white-space: nowrap;
  }
  .contact--left { left: 34px; bottom: 56px; }
  .contact--right { right: 40px; bottom: 40px; }
</style>
</head>
<body>
  <main class="canvas">
    <section class="card card--back" aria-label="Business card, contact side">
      <span class="accent-bar accent-bar--left"></span>
      <span class="accent-bar accent-bar--right"></span>
      <div class="person">
        <p class="person__name">Dana Whitlow</p>
        <p class="person__title">Designer Artist</p>
      </div>
      <div class="contact contact--left">
        <p>+61-0400-000-000</p>
        <p>Harrowdene, Australia</p>
      </div>
      <div class="contact contact--right">
        <p>dana.whitlow@quelbrook-insights.example</p>
        <p>www.quelbrook-insights.example</p>
      </div>
    </section>

    <section class="card card--front" aria-label="Business card, brand side">
      <h1 class="brand-name">QUELBROOK INSIGHTS</h1>
      <p class="tagline">TRACK, REVIEW, RETAIN</p>
    </section>
  </main>
</body>
</html>
```